Website design with eCommerce for revolutionary new product in the manufacturing industry.

We need a website designed for a precision manufacturing company based in the suburbs of Minneapolis, Minnesota called Velkrin Manufacturing. We have a revolutionary new product, the TARN LOCK, to introduce and sell through an eCommerce storefront. The website would include company information, product information, and the storefront. Green is a color that represents Velkrin Manufacturing. The final design should communicate that we exclusively offer premium products at a premium price. The design should also let the customer know they are the focus of our work.

Target Market(s)

Machinists and machine shops

Industry/Entity Type

Manufacturing and machine shops

Coding

Coded - Design and coding required

Font styles to use
Sans Serif

Colors
59FF00
82FF00
B8FF75
E3FFCB
F4FFEA

Requirements
Must have
• eCommerce storefront, Made in USA references
Nice to have
• Home page, TARN LOCK Product page, About Us, Capabilities, Contact, etc.
Should not have
• Should not be too much text and reading.

```html
<!DOCTYPE html>
<html lang="en">
<head>
<meta charset="utf-8">
<title>Gallery – Velkrin Manufacturing</title>
<link href="https://fonts.googleapis.com/css2?family=Poppins:wght@400;500;600;700;800&display=swap" rel="stylesheet">
<style>
:root{
  --green:#59ff00;
  --ink:#111111;
  --footer:#161616;
  --field:#2b2b2b;
  --white:#ffffff;
  --muted:#3a3a3a;
}
*{margin:0;padding:0;box-sizing:border-box}
html,body{width:723px;height:1200px;overflow:hidden}
body{font-family:'Poppins',sans-serif;background:var(--white);color:var(--ink);position:relative}

.site-header{position:absolute;left:0;top:0;width:723px;height:46px;background:var(--white)}
.brand{position:absolute;left:54px;top:12px;display:flex;align-items:center;gap:6px;font-weight:800;font-size:17px;letter-spacing:.8px;color:var(--ink)}
.brand .mark{width:12px;height:12px;background:var(--ink)}
.main-nav{position:absolute;left:192px;top:19px;display:flex;gap:11.5px;font-size:7.2px;font-weight:500}
.main-nav a{color:var(--ink);text-decoration:none}
.main-nav a.active{color:var(--green)}
.nav-contact{position:absolute;left:660px;top:0;width:63px;height:46px;background:var(--green);font-size:7.5px;font-weight:700;display:flex;align-items:center;justify-content:center;padding-bottom:2px}

.hero{position:absolute;left:0;top:46px;width:723px;height:236px;background:
  radial-gradient(ellipse at 30% 40%,rgba(190,188,182,.55),transparent 55%),
  radial-gradient(ellipse at 75% 60%,rgba(170,168,162,.5),transparent 55%),
  linear-gradient(160deg,#3f3b36 0%,#7c7a75 40%,#5b5650 70%,#3a3632 100%)}
.hero-slant{position:absolute;left:0;top:0}
.hero-title{position:absolute;left:0;top:114px;width:723px;text-align:center;color:var(--white);font-weight:800;font-size:37px;letter-spacing:.5px}

.section-title{position:absolute;left:0;top:304px;width:723px;text-align:center;font-weight:800;font-size:24px}
.title-rule{position:absolute;left:336px;top:341px;width:51px;height:2px;background:var(--green)}
.section-lead{position:absolute;left:0;top:356px;width:723px;text-align:center;font-size:8.6px;color:var(--muted)}

.tile{position:absolute;border-radius:8px;overflow:hidden}
.tile-rings{left:53px;top:396px;width:119px;height:165px;background:
  radial-gradient(circle at 30% 30%,rgba(235,235,235,.8),transparent 45%),
  radial-gradient(circle at 70% 70%,rgba(220,215,205,.7),transparent 45%),
  linear-gradient(135deg,#c8b188,#9d9588 50%,#b59b70)}
.tile-part{left:177px;top:396px;width:119px;height:165px;background:
  radial-gradient(ellipse at 80% 55%,rgba(200,200,195,.55),transparent 40%),
  linear-gradient(135deg,#4f4f4c,#2c2c2a 60%,#3e3e3b)}
.tile-tri{left:302px;top:396px;width:119px;height:165px;background:
  radial-gradient(circle at 50% 30%,rgba(210,208,204,.6),transparent 50%),
  radial-gradient(circle at 50% 80%,rgba(190,188,184,.5),transparent 50%),
  linear-gradient(135deg,#6b5b45,#9a9894 50%,#6b5b45)}
.tile-pins{left:425px;top:396px;width:243px;height:165px;background:
  radial-gradient(ellipse at 55% 30%,rgba(215,215,212,.75),transparent 45%),
  linear-gradient(180deg,#5a5a58,#9d9d9a 55%,#4a4a48)}
.tile-chips{left:53px;top:567px;width:244px;height:165px;background:
  radial-gradient(ellipse at 30% 40%,rgba(200,200,198,.5),transparent 50%),
  radial-gradient(ellipse at 75% 70%,rgba(180,180,178,.45),transparent 50%),
  linear-gradient(135deg,#6a6a68,#3e3e3c 50%,#7a7a78)}
.tile-disc{left:301px;top:567px;width:119px;height:165px;background:
  radial-gradient(circle at 50% 45%,rgba(225,224,220,.9),transparent 40%),
  linear-gradient(180deg,#a3a19c,#7d7b77 60%,#9b9994)}
.tile-brass{left:425px;top:567px;width:119px;height:165px;background:
  radial-gradient(ellipse at 35% 30%,rgba(214,176,112,.85),transparent 38%),
  radial-gradient(ellipse at 75% 75%,rgba(214,176,112,.8),transparent 35%),
  linear-gradient(135deg,#1e55a8,#1a4a94)}
.tile-spiral{left:550px;top:567px;width:118px;height:165px;background:
  radial-gradient(ellipse at 50% 50%,rgba(160,175,200,.55),transparent 55%),
  linear-gradient(135deg,#1a2546,#55648a 50%,#1c2848)}

.btn-more{position:absolute;left:328px;top:781px;width:67px;height:24px;background:var(--ink);color:var(--white);border-radius:3px;font-size:7px;font-weight:700;display:flex;align-items:center;justify-content:center}

.site-footer{position:absolute;left:0;top:867px;width:723px;height:333px;background:var(--footer);color:var(--white)}
.footer-shape{position:absolute;left:0;top:0}
.footer-brand{position:absolute;left:54px;top:32px;display:flex;align-items:center;gap:6px;font-weight:800;font-size:17px;letter-spacing:.8px}
.footer-brand .mark{width:12px;height:12px;background:var(--white)}
.footer-tag{position:absolute;left:214px;top:31px;width:160px;font-size:8.5px;line-height:13.5px}
.call{position:absolute;left:474px;top:35px;display:flex;align-items:center;color:var(--ink)}
.call-icon{width:28px;height:26px;background:var(--ink);border-radius:2px;display:flex;align-items:center;justify-content:center}
.call-label{font-size:8px;font-weight:600;margin:4px 6px 0 7px}
.call-number{font-size:16.5px;font-weight:700}

.col-head{position:absolute;top:122px;font-size:11px;font-weight:700}
.link-list{position:absolute;top:149px;list-style:none;font-size:7px;line-height:13.4px}
.social{position:absolute;left:223px;top:144px;list-style:none;font-size:7px}
.social li{display:flex;align-items:center;gap:5px;height:21.3px}
.social .sq{width:15px;height:15px;background:var(--field);border-radius:2px}
.contact-list{position:absolute;left:338px;top:150px;list-style:none;font-size:7.6px;line-height:11.5px}
.contact-list li{display:flex;gap:5px;margin-bottom:9px}
.contact-list svg{flex:none;margin-top:1px}
.field{position:absolute;left:484px;width:155px;height:20px;background:var(--field);border-radius:2px;font-size:7px;color:#cfcfcf;padding:5px 8px}
.submit{position:absolute;left:484px;top:227px;width:54px;height:20px;background:var(--white);color:var(--ink);border-radius:2px;font-size:7.5px;font-weight:700;display:flex;align-items:center;justify-content:center}
.footer-rule{position:absolute;left:55px;top:293px;width:616px;height:1px;background:#3a3a3a}
.copyright{position:absolute;left:0;top:308px;width:723px;text-align:center;font-size:7.5px;font-weight:600}
.to-top{position:absolute;left:681px;top:281px;width:28px;height:26px;background:var(--green);display:flex;align-items:center;justify-content:center}
</style>
</head>
<body>

<header class="site-header">
  <div class="brand"><span class="mark"></span>TARN LOCK</div>
  <nav class="main-nav">
    <a href="#">WHY VELKRIN MANUFACTURING?</a>
    <a href="#">WHAT WE DO</a>
    <a href="#">HOW WE MAKE IT BETTER</a>
    <a href="#">CAPABILITIES</a>
    <a href="#" class="active">GALLERY</a>
    <a href="#">ABOUT US</a>
    <a href="#">WISDOM</a>
  </nav>
  <div class="nav-contact">CONTACT</div>
</header>

<section class="hero" role="img" aria-label="Rows of machined aluminium parts on a wooden surface">
  <svg class="hero-slant" width="723" height="236" viewBox="0 0 723 236">
    <polygon points="0,236 723,123 723,153" fill="#59ff00"/>
    <polygon points="0,236 723,153 723,236" fill="#ffffff"/>
  </svg>
</section>
<h1 class="hero-title">GALLERY</h1>

<h2 class="section-title">OUR PROJECTS</h2>
<div class="title-rule"></div>
<p class="section-lead">Here are some of the projects we've created over the years.</p>

<div class="tile tile-rings" role="img" aria-label="Machined metal rings laid out in rows on wood"></div>
<div class="tile tile-part" role="img" aria-label="Close-up of a dark anodised machined part"></div>
<div class="tile tile-tri" role="img" aria-label="Grid of triangular machined aluminium parts"></div>
<div class="tile tile-pins" role="img" aria-label="Machined plate covered with cylindrical pins"></div>
<div class="tile tile-chips" role="img" aria-label="Pile of metal machining chips"></div>
<div class="tile tile-disc" role="img" aria-label="Perforated machined metal disc"></div>
<div class="tile tile-brass" role="img" aria-label="Brass machined blocks on a blue surface"></div>
<div class="tile tile-spiral" role="img" aria-label="Blue metal spiral turnings"></div>

<div class="btn-more">LOAD MORE</div>

<footer class="site-footer">
  <svg class="footer-shape" width="723" height="75" viewBox="0 0 723 75">
    <polygon points="387,0 723,0 723,21 396,21" fill="#ffffff"/>
    <polygon points="396,21 723,21 723,74 419,74" fill="#59ff00"/>
  </svg>
  <div class="footer-brand"><span class="mark"></span>TARN LOCK</div>
  <p class="footer-tag">Velkrin Manufacturing has humble roots, starting as many machine</p>
  <div class="call">
    <div class="call-icon">
      <svg width="11" height="11" viewBox="0 0 24 24"><path fill="#fff" d="M6.6 10.8a15.1 15.1 0 0 0 6.6 6.6l2.2-2.2c.3-.3.7-.4 1-.2 1.1.4 2.3.6 3.6.6.6 0 1 .4 1 1V20c0 .6-.4 1-1 1A17 17 0 0 1 3 4c0-.6.4-1 1-1h3.5c.6 0 1 .4 1 1 0 1.3.2 2.5.6 3.6.1.3 0 .7-.2 1z"/></svg>
    </div>
    <span class="call-label">Call us:</span>
    <span class="call-number">+123 456 7890</span>
  </div>

  <h3 class="col-head" style="left:87px">Helpful Links</h3>
  <ul class="link-list" style="left:87px">
    <li>Why Velkrin manufacturing?</li>
    <li>What We Do</li>
    <li>How We Make It Better</li>
    <li>Capabilities</li>
    <li>Gallery</li>
    <li>About Us</li>
    <li>Wisdom</li>
    <li>Contact Us</li>
  </ul>

  <h3 class="col-head" style="left:226px">Information</h3>
  <ul class="social">
    <li><span class="sq"></span>Newsfeed</li>
    <li><span class="sq"></span>Updates</li>
    <li><span class="sq"></span>Reviews</li>
    <li><span class="sq"></span>Careers</li>
    <li><span class="sq"></span>Videos</li>
  </ul>

  <h3 class="col-head" style="left:338px">Contact Us</h3>
  <ul class="contact-list">
    <li><svg width="8" height="7" viewBox="0 0 16 12"><rect width="16" height="12" rx="1" fill="#59ff00"/><path d="M1 1l7 5 7-5" stroke="#161616" stroke-width="1.5" fill="none"/></svg><span>Email:<br>info@tarnlock-mfg.com</span></li>
    <li><svg width="8" height="8" viewBox="0 0 24 24"><path fill="#59ff00" d="M6.6 10.8a15.1 15.1 0 0 0 6.6 6.6l2.2-2.2c.3-.3.7-.4 1-.2 1.1.4 2.3.6 3.6.6.6 0 1 .4 1 1V20c0 .6-.4 1-1 1A17 17 0 0 1 3 4c0-.6.4-1 1-1h3.5c.6 0 1 .4 1 1 0 1.3.2 2.5.6 3.6.1.3 0 .7-.2 1z"/></svg><span>Phone:<br>+08 123 456 7890</span></li>
    <li><svg width="7" height="9" viewBox="0 0 12 16"><path fill="#59ff00" d="M6 0a6 6 0 0 0-6 6c0 4.5 6 10 6 10s6-5.5 6-10a6 6 0 0 0-6-6zm0 8.5A2.5 2.5 0 1 1 6 3.5a2.5 2.5 0 0 1 0 5z"/></svg><span>Location:<br>Some address line goes<br>here city name</span></li>
  </ul>

  <h3 class="col-head" style="left:483px">Get in Touch</h3>
  <div class="field" style="top:148px">Enter Name</div>
  <div class="field" style="top:172px">Enter Company</div>
  <div class="field" style="top:197px">Enter Country</div>
  <div class="submit">SUBMIT</div>

  <div class="footer-rule"></div>
  <p class="copyright">©COPYRIGHT 2022 TARN LOCK, ALL RIGHTS RESERVED</p>
  <div class="to-top">
    <svg width="8" height="10" viewBox="0 0 8 10"><path d="M4 10V1M1 4l3-3 3 3" stroke="#111" stroke-width="1" fill="none"/></svg>
  </div>
</footer>

</body>
</html>
```